MRT Property - Business Cards

Looking for a business card & general letterhead, signage etc design for our new logo.

Colours:
000a20
0056a2
00b5ef
0088ce
68cef2

Fonts:
Poppins
Karla

Please keep look and feel of new brand - example in the zip package I sent.

```html
<!DOCTYPE html>
<html lang="en">
<head>
<meta charset="utf-8">
<title>MRT Property – Business Cards</title>
<link href="https://fonts.googleapis.com/css2?family=Poppins:wght@500;700&family=Karla:wght@400;500&display=swap" rel="stylesheet">
<style>
  :root {
    --stage: #242424;
    --card: #0b1120;
    --navy: #000a20;
    --brand-blue: #0056a2;
    --cyan: #00b5ef;
    --mid-blue: #0088ce;
    --light-blue: #68cef2;
    --white: #ffffff;
  }
  * { box-sizing: border-box; margin: 0; padding: 0; }
  html, body { width: 1200px; height: 780px; overflow: hidden; }
  body {
    background: var(--stage);
    font-family: "Karla", sans-serif;
    display: flex;
    flex-direction: column;
    align-items: center;
    justify-content: center;
    gap: 40px;
  }
  .card {
    position: relative;
    width: 600px;
    height: 340px;
    background: var(--card);
    border-radius: 28px;
    border-bottom: 4px solid var(--cyan);
    border-left: 2px solid var(--cyan);
    border-right: 2px solid var(--cyan);
    box-shadow: 0 14px 28px rgba(0,0,0,.55);
    overflow: hidden;
  }
  .wordmark {
    font-family: "Poppins", sans-serif;
    font-weight: 700;
    color: var(--brand-blue);
    display: flex;
    align-items: center;
    gap: 14px;
    letter-spacing: .5px;
  }
  .wordmark .dot {
    border-radius: 50%;
    background: var(--brand-blue);
    flex: none;
  }
  .card-front { display: flex; align-items: center; justify-content: center; }
  .card-front .wordmark { font-size: 52px; }
  .card-front .dot { width: 44px; height: 44px; }

  .card-back .wordmark {
    position: absolute; left: 44px; top: 44px; font-size: 30px;
  }
  .card-back .dot { width: 26px; height: 26px; }
  .holder {
    position: absolute; right: 0; top: 48px;
    padding-right: 44px;
    text-align: right;
  }
  .holder::after {
    content: ""; position: absolute; right: 0; top: 0;
    width: 18px; height: 58px; background: var(--brand-blue);
  }
  .holder-name {
    font-family: "Poppins", sans-serif; font-weight: 700;
    font-size: 22px; color: var(--brand-blue); letter-spacing: 1px;
    line-height: 1.2;
  }
  .holder-role { font-size: 15px; color: var(--white); letter-spacing: .5px; }
  .contact {
    position: absolute; left: 84px; bottom: 34px;
    color: var(--white); font-size: 16px; line-height: 1.35;
  }
  .address { margin-bottom: 22px; }
  .contact-list { list-style: none; }
  .contact-list li { display: flex; align-items: center; gap: 8px; }
  .contact-list svg { width: 14px; height: 14px; fill: var(--cyan); flex: none; }
</style>
</head>
<body>
  <section class="card card-front" aria-label="Card front">
    <div class="wordmark"><span class="dot"></span>MRT Property</div>
  </section>

  <section class="card card-back" aria-label="Card back">
    <div class="wordmark"><span class="dot"></span>MRT Property</div>
    <div class="holder">
      <p class="holder-name">DANIEL REYES</p>
      <p class="holder-role">Managing Director</p>
    </div>
    <div class="contact">
      <p class="address">Your address, City<br>State, Zip 1234</p>
      <ul class="contact-list">
        <li><svg viewBox="0 0 24 24"><path d="M6.6 10.8a15.1 15.1 0 0 0 6.6 6.6l2.2-2.2a1 1 0 0 1 1-.25 11.4 11.4 0 0 0 3.6.57 1 1 0 0 1 1 1V20a1 1 0 0 1-1 1A17 17 0 0 1 3 4a1 1 0 0 1 1-1h3.5a1 1 0 0 1 1 1c0 1.25.2 2.45.57 3.57a1 1 0 0 1-.25 1z"/></svg>123 456 789</li>
        <li><svg viewBox="0 0 24 24"><path d="M2 5h20v14H2zm2 2v.5l8 5 8-5V7zm0 2.8V17h16V9.8l-8 5z"/></svg>info@yourgmail.com</li>
        <li><svg viewBox="0 0 24 24"><path d="M12 2a10 10 0 1 0 0 20 10 10 0 0 0 0-20zm6.9 6h-3a15 15 0 0 0-1.3-3.9A8 8 0 0 1 18.9 8zM12 4c.8 1.2 1.5 2.5 1.9 4h-3.8c.4-1.5 1.1-2.8 1.9-4zM4.3 14a8 8 0 0 1 0-4h3.4a16 16 0 0 0 0 4zm.8 2h3a15 15 0 0 0 1.3 3.9A8 8 0 0 1 5.1 16zm3-8h-3a8 8 0 0 1 4.3-3.9A15 15 0 0 0 8.1 8zM12 20c-.8-1.2-1.5-2.5-1.9-4h3.8c-.4 1.5-1.1 2.8-1.9 4zm2.3-6H9.7a14 14 0 0 1 0-4h4.6a14 14 0 0 1 0 4zm.3 5.9a15 15 0 0 0 1.3-3.9h3a8 8 0 0 1-4.3 3.9zm1.7-5.9a16 16 0 0 0 0-4h3.4a8 8 0 0 1 0 4z"/></svg>www.yourwebsite.com</li>
      </ul>
    </div>
  </section>
</body>
</html>
```